Online media outlet needs a blog and logo

A new online blog platform is being established in the UK. The blog will be very similar in layout to www.quorvel.co. It will need to have a main story slider showing three slides and block tiles beneath the slider for additional tiles.

The blog platform will be called 'Tandrel Brisk' and will also need a professional looking logo design for the name.

The website should be designed in Word Press.

Industry/Entity Type

Media

Logo Text

Tandrel Brisk

Coding

Coded - Design and coding required

Number of Pages Required

3 page

Font styles to use
Other font styles liked:
• Helvetica

Requirements
Must have
• A slider showing three slides. Be similar to Quor V (see previous comment). Be Word Press compatible.

```html
<!DOCTYPE html>
<html lang="en">
<head>
<meta charset="utf-8">
<title>Tandrel Brisk</title>
<link rel="stylesheet" href="https://fonts.googleapis.com/css2?family=Lato:wght@400;700;900&family=Raleway:wght@300;400;600&display=swap">
<style>
:root{
  --red:#d42a2a;
  --ink:#1e1e1e;
  --topbar:#161616;
  --header:#1c1c1c;
  --panel:#f3f3f3;
  --white:#ffffff;
  --muted:#777777;
  --text:#333333;
  --foot:#f1f1f1;
  --line:#e2e2e2;
}
*{box-sizing:border-box;margin:0;padding:0}
html,body{width:1200px;height:3255px;overflow:hidden}
body{font-family:"Lato",Helvetica,Arial,sans-serif;color:var(--text);background:var(--white);position:relative}
.abs{position:absolute}

/* top bar */
.topbar{left:0;top:0;width:1200px;height:43px;background:var(--topbar)}
.social{left:98px;top:12px;display:flex;gap:12px}
.social span{width:19px;height:19px;border-radius:50%;background:#4a4a4a;display:block}
.util{right:98px;top:14px;display:flex;gap:22px;font-size:10px;font-weight:700;color:#ddd;letter-spacing:.5px}
.util .dot{width:9px;height:9px;border-radius:50%;border:2px solid #ddd;display:inline-block;margin-right:5px;vertical-align:-1px}

/* header */
.header{left:0;top:43px;width:1200px;height:61px;background:var(--header)}
.logo{left:98px;top:12px;font-family:"Lato",sans-serif;font-size:33px;font-weight:400;color:var(--white)}
.nav{right:98px;top:18px;display:flex;gap:6px;font-size:10px;font-weight:700;color:var(--white)}
.nav a{padding:7px 11px;color:inherit;text-decoration:none}
.nav a.on{background:var(--red)}

/* hero */
.hero{left:0;top:104px;width:1200px;height:478px;background:linear-gradient(90deg,#141414 0%,#1b1b1b 42%,#2a3a4a 62%,#4b6a86 78%,#1d2530 100%)}
.hero-art{left:560px;top:0;width:640px;height:478px;background:radial-gradient(ellipse at 45% 55%,rgba(180,210,235,.55),rgba(40,60,80,.25) 55%,rgba(0,0,0,0) 75%)}
.badge{left:98px;top:103px;background:var(--white);color:var(--ink);font-size:10px;font-weight:700;padding:6px 14px;clip-path:polygon(0 0,100% 0,92% 100%,0 100%)}
.hero h1{left:98px;top:143px;width:520px;font-family:"Raleway",sans-serif;font-weight:300;font-size:31px;line-height:40px;color:var(--white)}
.btn{left:98px;top:301px;background:var(--red);color:var(--white);font-size:12px;font-weight:700;width:150px;height:42px;line-height:42px;text-align:center}
.dots{left:578px;top:455px;display:flex;gap:6px}
.dots span{width:6px;height:6px;border-radius:50%;background:#fff}
.dots span:first-child{background:var(--red)}

/* tabs */
.tabs{left:0;top:582px;width:1200px;height:80px;background:var(--white);border-bottom:1px solid var(--line)}
.tabs ul{position:absolute;left:98px;top:0;display:flex;list-style:none;font-size:10px;color:#555;font-weight:700}
.tabs li{height:80px;line-height:80px;width:160px;text-align:center}
.tabs li.on{background:var(--panel);color:var(--ink)}

.panel{left:0;top:662px;width:1200px;height:850px;background:var(--panel)}

/* tiles */
.tile{position:absolute;overflow:hidden;color:var(--white)}
.tile .tag{position:absolute;left:0;top:26px;background:var(--red);font-size:10px;padding:5px 22px 5px 10px;clip-path:polygon(0 0,100% 0,88% 100%,0 100%)}
.tile .ttl{position:absolute;left:18px;right:18px;bottom:48px;font-weight:900;font-size:15px;line-height:20px}
.tile .meta{position:absolute;left:18px;bottom:20px;font-size:9px;font-weight:900;letter-spacing:.3px}
.tile .ic{position:absolute;right:18px;bottom:20px;width:11px;height:11px;border-radius:50%;background:var(--white)}
.tile.big .ttl{font-size:20px;line-height:27px;bottom:55px}
.tile.big .meta{font-size:11px}
.p1{background:linear-gradient(160deg,#8a8f94,#5b4a40 55%,#2a2624)}
.p2{background:linear-gradient(160deg,#6a5f58,#3a3431 60%,#222)}
.p3{background:linear-gradient(160deg,#7a5a45,#4a3a30 60%,#2a2220)}
.p4{background:linear-gradient(160deg,#9a6a3a,#5a3b26 60%,#2a1d15)}
.p5{background:linear-gradient(160deg,#5b6f85,#2a2a30 50%,#141414)}
.p6{background:linear-gradient(160deg,#8a7a55,#5a4a38 60%,#2a241c)}
.p7{background:linear-gradient(160deg,#a98a6a,#6a5040 60%,#2a2018)}
.p8{background:linear-gradient(160deg,#9ab070,#6a7a4a 55%,#34361f)}
.tile::after{content:"";position:absolute;inset:0;background:linear-gradient(180deg,rgba(0,0,0,0) 45%,rgba(0,0,0,.55))}
.tile>*{z-index:1}

.card{position:absolute;background:var(--white);padding:22px 22px 0 22px}
.card .kick{font-size:10px;color:#444;margin-bottom:12px}
.card h3{font-size:15px;line-height:21px;font-weight:900;color:var(--ink);margin-bottom:12px}
.card p{font-size:10px;line-height:16px;color:#666}
.card .meta{position:absolute;left:22px;bottom:22px;font-size:9px;font-weight:700;color:#333}
.card .ic{position:absolute;right:22px;bottom:22px;width:11px;height:11px;border-radius:50%;background:var(--ink)}

/* newsletter */
.news{left:0;top:1512px;width:1200px;height:330px;background:linear-gradient(180deg,#1f1a1c 0%,#3a2a24 55%,#5a3a22 100%)}
.news h2{position:absolute;left:0;width:1200px;top:77px;text-align:center;font-size:22px;font-weight:700;color:var(--white);letter-spacing:.5px}
.news p{position:absolute;left:130px;width:940px;top:117px;text-align:center;font-size:11px;line-height:18px;color:#cfc6c0}
.field{position:absolute;top:205px;height:40px;background:var(--white);font-size:11px;color:#555;padding:13px 16px}
.sub{position:absolute;left:818px;top:205px;width:168px;height:40px;background:var(--red);color:var(--white);font-size:13px;text-align:center;line-height:40px}

.spinner{left:585px;top:2762px}

/* footer */
.footer{left:0;top:2832px;width:1200px;height:354px;background:var(--foot)}
.footer h4{position:absolute;top:62px;font-size:13px;font-weight:900;color:var(--red)}
.footer p{position:absolute;left:98px;top:120px;width:370px;font-size:10px;line-height:17px;color:#888}
.footer ul{position:absolute;top:117px;list-style:none;font-size:11px;color:#888;line-height:36px}
.bottom{left:0;top:3186px;width:1200px;height:69px;background:var(--ink);color:#ddd;font-size:12px;text-align:center;line-height:69px}
</style>
</head>
<body>

<div class="abs topbar">
  <div class="abs social"><span></span><span></span><span></span></div>
  <div class="abs util"><span><i class="dot"></i>LANGUAGES</span><span>SUPPORT</span><span>LOG IN</span><span><i class="dot"></i></span></div>
</div>

<header class="abs header">
  <div class="abs logo">Tandrel Brisk</div>
  <nav class="abs nav"><a class="on">HOME</a><a>ABOUT US</a><a>GALLERY</a><a>ALL TOPICS</a><a>FEATURES</a><a>CONTACT US</a></nav>
</header>

<section class="abs hero">
  <div class="abs hero-art" role="img" aria-label="Hand holding a glowing laptop with a network of digital icons over a world map"></div>
  <div class="abs badge">TOP STORY</div>
  <h1 class="abs">Lorem ipsum dolor sit amet, consectetur adipiscing elit. Nunc molestie</h1>
  <div class="abs btn">READ MORE</div>
  <div class="abs dots"><span></span><span></span><span></span><span></span></div>
</section>

<div class="abs tabs"><ul><li class="on">CURRENT TOPICS</li><li>MEDIA</li><li>GOVERNMENT</li><li>POLITICS</li><li>COMPETITION</li><li>INVESTMENT</li><li>OTHER</li></ul></div>

<div class="abs panel"></div>

<article class="tile big p1" style="left:98px;top:720px;width:514px;height:489px" role="img" aria-label="Smiling woman in a denim shirt working at a desk">
  <span class="tag">Lorem ipsum dolor</span>
  <div class="ttl">Sed justo libero, finibus sed enim sit amet, pulvinar condimentum sapien.</div>
  <div class="meta">LOREM IPSUM DOLOR SIT AMET - MAY 2016</div><span class="ic"></span>
</article>
<article class="tile p2" style="left:621px;top:720px;width:234px;height:224px" role="img" aria-label="Businessman in a suit">
  <span class="tag">Contentry Popular</span>
  <div class="ttl">Sed justo libero, finibus sed enim sit amet</div>
  <div class="meta">DOLOR SIT AMET - MAY 2016</div><span class="ic"></span>
</article>
<article class="tile p2" style="left:864px;top:720px;width:236px;height:224px" role="img" aria-label="Businessman in an office">
  <span class="tag">Popilar Sit Amit</span>
  <div class="ttl">Sed justo libero, finibus sed enim sit amet</div>
  <div class="meta">DOLOR SIT AMET - MAY 2016</div><span class="ic"></span>
</article>
<article class="card" style="left:621px;top:950px;width:479px;height:259px">
  <div class="kick">Dolr Sit Lorem</div>
  <h3>Sed justo libero, finibus sed enim sit amet, pulvinar condimentum sapien.</h3>
  <p>Vestibulum vitae metus ut arcu commodo vulputate rutrum et metus. Donec eget risus magna. Nullam bibendum nunc ac nulla faucibus, at consectetur nisl consectetur. Nulla eget eros suscipit, sagittis tellus et, eleifend magna. Curabitur cursus malesuada neque eget commodo. Etiam imperdiet felis id mollis pulvinar.</p>
  <div class="meta">LOREM IPSUM DOLOR SIT AMET - MAY 2016</div><span class="ic"></span>
</article>
<article class="card" style="left:98px;top:1220px;width:514px;height:223px">
  <div class="kick">Dolr Sit Lorem</div>
  <h3>Vestibulum vitae metus ut arcu commodo vulputate rutrum et metus. Donec eget risus magna</h3>
  <p>Vestibulum vitae metus ut arcu commodo vulputate rutrum et metus. Donec eget risus magna. Nullam bibendum nunc ac nulla faucibus, at consectetur nisl consectetur. Nulla eget eros suscipit, sagittis tellus et, eleifend magna.</p>
  <div class="meta">LOREM IPSUM DOLOR SIT AMET - MAY 2016</div><span class="ic"></span>
</article>
<article class="tile p3" style="left:621px;top:1220px;width:234px;height:223px" role="img" aria-label="Smiling man in a café">
  <span class="tag">Contentry Popular</span>
  <div class="ttl">Sed justo libero, finibus sed enim sit amet</div>
  <div class="meta">DOLOR SIT AMET - MAY 2016</div><span class="ic"></span>
</article>
<article class="tile p3" style="left:864px;top:1220px;width:236px;height:223px" role="img" aria-label="Group of colleagues in a meeting">
  <span class="tag">Popilar Sit Amit</span>
  <div class="ttl">Sed justo libero, finibus sed enim sit amet</div>
  <div class="meta">DOLOR SIT AMET - MAY 2016</div><span class="ic"></span>
</article>

<section class="abs news" role="img" aria-label="Blurred city bridge at dusk behind the newsletter form">
  <h2>SUBSCRIBE FOR NEWSLETTER</h2>
  <p>Lorem ipsum dolor sit amet, consectetur adipiscing elit. Nunc molestie hendrerit tincidunt. Mauris tellus nisl, viverra sed mollis in, faucibus nec risus. Etiam finibus, orci sit amet finibus ultrices, purus ex efficitur sem, id venenatis sapien felis id dui. Ut commodo pulvinar orci.</p>
  <div class="field" style="left:236px;width:288px">Name</div>
  <div class="field" style="left:528px;width:286px">Email</div>
  <div class="sub">SUBSCRIBE</div>
</section>

<article class="tile p4" style="left:98px;top:1918px;width:236px;height:224px" role="img" aria-label="Cyclist riding at sunset">
  <span class="tag">Contentry Popular</span>
  <div class="ttl">Sed justo libero, finibus sed enim sit amet</div>
  <div class="meta">DOLOR SIT AMET - MAY 2016</div><span class="ic"></span>
</article>
<article class="tile p4" style="left:341px;top:1918px;width:236px;height:224px" role="img" aria-label="Friends laughing outdoors in warm light">
  <span class="tag">Popilar Sit Amit</span>
  <div class="ttl">Sed justo libero, finibus sed enim sit amet</div>
  <div class="meta">DOLOR SIT AMET - MAY 2016</div><span class="ic"></span>
</article>
<article class="card" style="left:98px;top:2148px;width:479px;height:258px">
  <div class="kick">Dolr Sit Lorem</div>
  <h3>Finibus sed enim sit amet, pulvinar condimentum sapien.</h3>
  <p>Vestibulum vitae metus ut arcu commodo vulputate rutrum et metus. Donec eget risus magna. Nullam bibendum nunc ac nulla faucibus, at consectetur nisl consectetur. Nulla eget eros suscipit, sagittis tellus et, eleifend magna. Curabitur cursus malesuada neque eget commodo. Etiam imperdiet felis id mollis pulvinar.</p>
  <div class="meta">LOREM IPSUM DOLOR SIT AMET - MAY 2016</div><span class="ic"></span>
</article>
<article class="tile big p5" style="left:586px;top:1918px;width:514px;height:488px" role="img" aria-label="Speaker in a suit surrounded by press microphones">
  <span class="tag">Lorem ipsum dolor</span>
  <div class="ttl">Justo libero, finibus sed enim sit amet, pulvinar condimentum sapien.</div>
  <div class="meta">LOREM IPSUM DOLOR SIT AMET - MAY 2016</div><span class="ic"></span>
</article>
<article class="tile big p6" style="left:98px;top:2417px;width:327px;height:313px" role="img" aria-label="Family group portrait outdoors">
  <span class="tag">Lorem sit dolor</span>
  <div class="ttl">Libero, finibus sed enim sit amet</div>
  <div class="meta">DOLOR SIT AMET - MAY 2016</div><span class="ic"></span>
</article>
<article class="tile big p7" style="left:436px;top:2417px;width:328px;height:313px" role="img" aria-label="City street with a bridge at golden hour">
  <span class="tag">Sit Amit Lorem</span>
  <div class="ttl">Finibus sed enim sit amet</div>
  <div class="meta">DOLOR SIT AMET - MAY 2016</div><span class="ic"></span>
</article>
<article class="tile big p8" style="left:775px;top:2417px;width:325px;height:313px" role="img" aria-label="Parents and children in a park">
  <span class="tag">Popilar Sit Amit</span>
  <div class="ttl">Loremd justo libero, finibus sed enim sit amet</div>
  <div class="meta">DOLOR SIT AMET - MAY 2016</div><span class="ic"></span>
</article>

<svg class="abs spinner" width="30" height="30" viewBox="0 0 30 30" aria-hidden="true">
  <g fill="#999"><circle cx="15" cy="3" r="2.5"/><circle cx="23.5" cy="6.5" r="2.3"/><circle cx="27" cy="15" r="2.1"/><circle cx="23.5" cy="23.5" r="1.9"/><circle cx="15" cy="27" r="1.7"/><circle cx="6.5" cy="23.5" r="1.5"/><circle cx="3" cy="15" r="1.3"/><circle cx="6.5" cy="6.5" r="1.1"/></g>
</svg>

<footer class="abs footer">
  <h4 style="left:98px">ABOUT US</h4>
  <p>Lorem ipsum dolor sit amet, consectetur adipiscing elit. Nunc molestie hendrerit tincidunt. Mauris tellus nisl, viverra sed mollis in, faucibus nec risus. Etiam finibus, orci sit amet finibus ultrices, purus ex efficitur sem, id venenatis sapien felis id dui.<br>Ut commodo pulvinar orci, sed congue lectus pretium sit amet. Aenean a mollis justo. Curabitur sit amet malesuada neque, vel feugiat nisl. Praesent ac pretium tellus.</p>
  <h4 style="left:529px">COMPANY</h4>
  <ul style="left:529px"><li>Home</li><li>Shop</li><li>About</li><li>How It Works</li><li>Contact</li></ul>
  <h4 style="left:742px">INFORMATION</h4>
  <ul style="left:742px"><li>Tearms &amp; Condition</li><li>Privacy Policy</li><li>How to Buy</li><li>How to Sell</li><li>Promotion</li></ul>
  <h4 style="left:990px">USEFUL LINKS</h4>
  <ul style="left:990px"><li>FAQ's</li><li>Services</li><li>Brows All</li></ul>
</footer>

<div class="abs bottom">© 2016 yoursite, All Rights Reserved.</div>

</body>
</html>
```